Dental Practice Website design

Design a new website for Brambleford Dental Practice.
Design should be warm, neutral in colour, with some small amount of bright colour if needed but kept to a minimum. Website should look professional, high end. Home page should be easy to navigate and simple for patients to be able to book online.
Logo in files along with some examples of websites that we like. Please ask if any further info needed.
Menu should have:
About
New Patients
Treatments
Fees
Contact Us

Industry/Entity Type

Dentistry

Number of Pages Required

4 page

Font styles to use
Sans Serif

Colors

Designer to choose colors to be used in the design.

Requirements
Must have
• Ravelle ratings badge, book online button,
Nice to have
• neutral, relaxing colours
Should not have
• harsh, bright colours!

```html
<!DOCTYPE html>
<html lang="en">
<head>
<meta charset="utf-8">
<title>Brambleford Dental Practice</title>
<link href="https://fonts.googleapis.com/css2?family=Nunito+Sans:wght@300;400;600;700;800&display=swap" rel="stylesheet">
<style>
:root{
  --ink:#1e2529;
  --dark:#1f2a2f;
  --text:#4a4f52;
  --muted:#7c8184;
  --band:#e4e5e4;
  --band-light:#eef0f0;
  --line:#c9cccd;
  --footer:#1b1c1d;
  --white:#ffffff;
  --star:#e8c53a;
}
*{box-sizing:border-box;margin:0;padding:0}
html,body{width:1200px;height:5089px;overflow:hidden}
body{font-family:"Nunito Sans",Arial,sans-serif;color:var(--text);background:var(--white);position:relative}
.abs{position:absolute}
.btn{position:absolute;display:flex;align-items:center;justify-content:center;border-radius:22px;font-weight:800;font-size:15px;letter-spacing:.3px;text-transform:uppercase}
.btn-dark{background:var(--dark);color:var(--white)}
.btn-light{background:var(--white);color:var(--ink)}
.btn-outline{border:2px solid var(--ink);color:var(--ink)}
.photo{position:absolute}
p.body{font-size:14.5px;line-height:30px;color:var(--text)}
h2.sec{font-weight:400;color:var(--ink);font-size:31px;letter-spacing:.5px}
h2.sec b{font-weight:800}

/* header */
.logo{position:absolute;display:flex;align-items:center;gap:10px}
.logo-mark{width:20px;height:20px;border:2px solid currentColor}
.logo-name{font-size:19px;font-weight:700;line-height:1.1;text-transform:uppercase;letter-spacing:.5px}
.contact-chip{position:absolute;display:flex;align-items:center;gap:12px;font-size:15px;color:var(--ink)}
.chip-icon{width:36px;height:36px;border-radius:50%;background:#f1f2f2;display:flex;align-items:center;justify-content:center}
.nav{position:absolute;top:68px;left:392px;display:flex;gap:0;font-size:15px;color:var(--ink);text-transform:uppercase}
.nav a{position:absolute;white-space:nowrap;color:inherit;text-decoration:none}
.nav a.active{font-weight:800;border-bottom:2px solid var(--ink);padding-bottom:3px}

/* hero */
.hero-title{color:var(--white)}
.arrow-btn{position:absolute;width:32px;height:32px;border-radius:50%;border:1.5px solid currentColor;display:flex;align-items:center;justify-content:center}

/* features */
.feature{position:absolute;width:390px}
.feature-icon{position:absolute;left:-98px;top:-12px;width:84px;height:84px;border-radius:50%;background:var(--white);border:1px solid #d4d6d6;box-shadow:0 0 0 6px #eceded;display:flex;align-items:center;justify-content:center}
.feature h3{font-size:28px;font-weight:400;color:var(--ink)}
.feature h3 b{font-weight:800}
.feature p{font-size:13px;line-height:25px;margin-top:8px}

/* services */
.service-text{position:absolute;width:400px;padding-left:36px;border-left:5px double #8d9193}
.service-text h3{font-size:24px;font-weight:800;color:var(--ink);letter-spacing:.8px;line-height:39px;text-transform:uppercase}
.service-text .rule{width:78px;height:3px;background:var(--ink);margin:12px 0 26px}
.service-text p{font-size:14px;line-height:30px}

/* testimonials */
.t-card{position:absolute;top:3910px;width:310px;height:185px;background:var(--white);border-radius:10px;box-shadow:0 2px 10px rgba(0,0,0,.12);text-align:center;padding:70px 24px 0;font-family:Arial,sans-serif;font-size:14px;line-height:25px;color:#555}
.t-avatar{position:absolute;top:-48px;left:111px;width:88px;height:88px;border-radius:50%;background:linear-gradient(#d8d3cc,#8aa3b4);border:3px solid var(--white)}
.t-badge{position:absolute;right:-4px;bottom:-2px;width:24px;height:24px;border-radius:50%;background:#cfd4d6;border:2px solid var(--white)}
.t-name{position:absolute;top:4122px;font-size:14px;font-weight:700;color:var(--ink);display:flex;gap:26px;align-items:center}
.stars{color:var(--star);letter-spacing:1px;font-size:13px}

/* footer */
.footer{position:absolute;left:0;top:4612px;width:1200px;height:477px;background:var(--footer);color:#d7d7d7}
.footer h4{position:absolute;font-size:21px;font-weight:700;color:var(--white)}
.footer ul{position:absolute;list-style:none;font-size:14px}
.footer li{height:31px;display:flex;align-items:center;gap:12px}
.f-contact{position:absolute;display:flex;align-items:center;gap:14px;font-size:14px}
.f-ci{width:36px;height:36px;border-radius:50%;background:var(--white);display:flex;align-items:center;justify-content:center}
.social{position:absolute;top:4866px;width:28px;height:28px;border-radius:50%;background:var(--white)}
</style>
</head>
<body>

<!-- HEADER -->
<header>
  <div class="logo" style="left:110px;top:30px;color:var(--ink)">
    <span class="logo-mark"></span>
    <span class="logo-name">Brambleford<br>Dental Practice</span>
  </div>
  <div class="contact-chip" style="left:450px;top:13px">
    <span class="chip-icon"><svg width="14" height="14" viewBox="0 0 24 24"><path fill="#1e2529" d="M6.6 10.8a15 15 0 006.6 6.6l2.2-2.2c.3-.3.7-.4 1-.2 1.1.4 2.3.6 3.6.6.6 0 1 .4 1 1V20c0 .6-.4 1-1 1A17 17 0 013 4c0-.6.4-1 1-1h3.5c.6 0 1 .4 1 1 0 1.3.2 2.5.6 3.6.1.3 0 .7-.2 1z"/></svg></span>
    +1 555 0142 7730
  </div>
  <div class="contact-chip" style="left:658px;top:13px">
    <span class="chip-icon"><svg width="15" height="12" viewBox="0 0 24 18"><path fill="#1e2529" d="M0 0h24v18H0zM2 2v1l10 7 10-7V2z"/></svg></span>
    hello@bramblefordental.com
  </div>
  <div class="btn btn-dark" style="left:917px;top:10px;width:170px;height:42px">Book Online</div>
  <nav class="nav">
    <a class="active" style="left:0">Home</a>
    <a style="left:98px">About</a>
    <a style="left:200px">New Patients</a>
    <a style="left:363px">Treatments</a>
    <a style="left:514px">Fees</a>
    <a style="left:599px">Contact Us</a>
  </nav>
</header>

<!-- HERO -->
<section>
  <div class="photo" role="img" aria-label="Smiling patient relaxing in a dental chair" style="left:0;top:104px;width:1200px;height:616px;background:linear-gradient(90deg,#3c3a38 0%,#6b6863 40%,#c9c6c1 65%,#a9a49d 100%)"></div>
  <svg class="abs" style="left:0;top:600px" width="1200" height="125" viewBox="0 0 1200 125">
    <polygon points="0,0 0,125 1200,125 1200,0 1150,20 1150,28 1095,108 105,108 50,28 50,20" fill="#fff" opacity="0"/>
    <polygon points="0,20 105,110 1095,110 1200,20 1200,125 0,125" fill="#fff"/>
    <polyline points="0,30 100,120 1100,120 1200,30" fill="none" stroke="#1e2529" stroke-width="6"/>
  </svg>
  <div class="abs hero-title" style="left:110px;top:233px;font-size:30px;font-weight:600;letter-spacing:.5px">WELCOME TO</div>
  <div class="abs hero-title" style="left:110px;top:282px;font-size:50px;line-height:58px;letter-spacing:.5px"><b style="font-weight:800">BRAMBLEFORD</b> <span style="font-weight:300">DENTAL<br>PRACTICE</span></div>
  <p class="abs" style="left:110px;top:408px;width:480px;font-size:14.5px;line-height:30px;color:var(--white)">We are passionate about improving dental health and helping you achieve your brightest smile and are honoured that you're considering us for your dental needs.</p>
  <div class="btn btn-light" style="left:110px;top:518px;width:172px;height:42px">Book Online</div>
  <div class="arrow-btn" style="left:40px;top:360px;color:var(--white)"><svg width="10" height="12" viewBox="0 0 10 12"><path d="M8 1L2 6l6 5" stroke="#fff" stroke-width="1.8" fill="none"/></svg></div>
  <div class="arrow-btn" style="left:1127px;top:360px;color:var(--white)"><svg width="10" height="12" viewBox="0 0 10 12"><path d="M2 1l6 5-6 5" stroke="#fff" stroke-width="1.8" fill="none"/></svg></div>
</section>

<!-- ABOUT -->
<section>
  <div class="photo" role="img" aria-label="Smiling woman during a dental check-up" style="left:110px;top:826px;width:433px;height:386px;border-radius:216px 216px 0 0/80px 80px 0 0;background:linear-gradient(160deg,#e7dccd,#b7a795 55%,#5e79a8)"></div>
  <h2 class="sec abs" style="left:620px;top:836px">ABOUT <span style="font-weight:400">US</span></h2>
  <div class="abs" style="left:620px;top:880px;width:36px;height:3px;background:var(--ink)"></div>
  <p class="body abs" style="left:620px;top:905px;width:468px">Welcome to our friendly dental practice nestled in the heart of beautiful Ashvale, UK. Our team of dedicated dentists, hygienists and support staff are here to provide you with exceptional dental care. With a wide array of services, including general and cosmetic dentistry, orthodontics and emergency care, we're confident that we can deliver the highest quality treatment to you and your loved ones. At our practice, we believe that a visit to the dentist should be a comfortable and positive experience.</p>
  <div class="btn btn-dark" style="left:620px;top:1172px;width:153px;height:42px">Read More</div>
</section>

<!-- FEATURES -->
<section>
  <div class="abs" style="left:0;top:1322px;width:1200px;height:492px;background:var(--band)"></div>
  <div class="feature" style="left:208px;top:1424px">
    <div class="feature-icon"><svg width="34" height="30" viewBox="0 0 34 30" fill="none" stroke="#555" stroke-width="1.5"><circle cx="17" cy="7" r="4"/><circle cx="7" cy="11" r="3"/><circle cx="27" cy="11" r="3"/><path d="M10 26c0-5 3-8 7-8s7 3 7 8M1 26c0-4 2-6 6-6M33 26c0-4-2-6-6-6"/></svg></div>
    <h3>OUR <b>TEAM</b></h3>
    <p>We are delighted to introduce you to our experienced and compassionate dental team. Our team comprises highly providing you with high-quality dental care services.</p>
  </div>
  <div class="feature" style="left:723px;top:1424px">
    <div class="feature-icon"><svg width="30" height="30" viewBox="0 0 30 30" fill="none" stroke="#555" stroke-width="1.5"><path d="M15 4c-6-3-11 1-10 8 1 5 3 6 4 14 1 2 3 2 3 0l2-7h2l2 7c0 2 2 2 3 0 1-8 3-9 4-14 1-7-4-11-10-8z"/></svg></div>
    <h3>OUR <b>PRACTICE</b></h3>
    <p>At our practice, we believe that a visit to the dentist should be a comfortable and positive experience. We strive to create a warm and welcoming atmosphere</p>
  </div>
  <div class="feature" style="left:208px;top:1601px">
    <div class="feature-icon"><svg width="30" height="30" viewBox="0 0 30 30" fill="none" stroke="#555" stroke-width="1.5"><path d="M10 5c-4-2-8 1-7 6 1 4 2 5 3 11 1 2 2 2 3 0l1-5h1l1 5c1 2 2 2 3 0 1-6 2-7 3-11"/><path d="M19 4l7 7M23 3l4 4-6 6-4-4z"/></svg></div>
    <h3>OUR <b>TREATMENTS</b></h3>
    <p>From our friendly reception staff to our knowledgeable hygienists and assistants, our team is here to ensure that you receive personalised dental care that meets your</p>
  </div>
  <div class="feature" style="left:723px;top:1601px">
    <div class="feature-icon"><svg width="30" height="30" viewBox="0 0 30 30" fill="none" stroke="#555" stroke-width="1.5"><rect x="5" y="8" width="20" height="17" rx="2"/><path d="M11 8V5h8v3M12 16h6M15 13v6"/></svg></div>
    <h3>OUR <b>PATIENTS</b></h3>
    <p>We understand that dental care can be expensive which is why we offer affordable prices to ensure that everyone has access to quality care.</p>
  </div>
</section>

<!-- SERVICES -->
<section>
  <h2 class="sec abs" style="left:0;top:1900px;width:1200px;text-align:center">OUR <b>SERVICES</b></h2>

  <div class="service-text" style="left:138px;top:1980px;height:320px;padding-top:22px">
    <h3>General and Cosmetic Dentistry</h3>
    <div class="rule"></div>
    <p>We strive to create a warm and welcoming atmosphere where our patients can feel at ease and confident in the care they receive.</p>
    <div class="btn btn-dark" style="position:relative;margin-top:22px;width:154px;height:42px">Read More</div>
  </div>
  <div class="photo" role="img" aria-label="Dentist comparing tooth shade samples with a patient" style="left:624px;top:1980px;width:426px;height:320px;background:linear-gradient(135deg,#c9ced3,#9aa4ab 50%,#c7c67a)"></div>

  <div class="photo" role="img" aria-label="Dentist examining a smiling patient's teeth" style="left:138px;top:2370px;width:424px;height:320px;background:linear-gradient(135deg,#cfc8c0,#7e8791 50%,#4f74a8)"></div>
  <div class="service-text" style="left:635px;top:2370px;height:320px;padding-top:38px">
    <h3>Orthodontics</h3>
    <div class="rule"></div>
    <p>Our state-of-the-art facilities and equipment mean that you can trust us to deliver the latest techniques and treatments to ensure your oral health is at its best.</p>
    <div class="btn btn-dark" style="position:relative;margin-top:22px;width:154px;height:42px">Read More</div>
  </div>

  <div class="service-text" style="left:138px;top:2760px;height:320px;padding-top:32px">
    <h3>Emergency Care</h3>
    <div class="rule"></div>
    <p>At our practice, we believe that a visit to the dentist should be a comfortable and positive experience. We strive to create a warm and welcoming atmosphere where our patients can feel the care they receive.</p>
    <div class="btn btn-dark" style="position:relative;margin-top:22px;width:154px;height:42px">Read More</div>
  </div>
  <div class="photo" role="img" aria-label="Dentist treating a patient with dental instruments" style="left:624px;top:2760px;width:426px;height:320px;background:linear-gradient(135deg,#5f86b5,#3b5f93 45%,#b7a79a)"></div>
</section>

<!-- SMILE -->
<section>
  <div class="abs" style="left:0;top:3190px;width:1200px;height:490px;background:var(--band-light)"></div>
  <div class="photo" role="img" aria-label="Before and after comparison of a whitened smile" style="left:112px;top:3292px;width:470px;height:288px;background:linear-gradient(90deg,#6e3a34,#b77a6a 30%,#c9b9a4 50%,#e9e3d8 70%,#8f4c44)"></div>
  <div class="abs" style="left:345px;top:3292px;width:2px;height:288px;background:var(--white)"></div>
  <div class="abs" style="left:323px;top:3414px;width:46px;height:46px;border-radius:50%;border:2px solid var(--white);display:flex;align-items:center;justify-content:center"><svg width="20" height="12" viewBox="0 0 20 12"><path d="M6 1L1 6l5 5M14 1l5 5-5 5" stroke="#fff" stroke-width="1.8" fill="none"/></svg></div>
  <h2 class="abs" style="left:636px;top:3296px;font-size:32px;line-height:43px;font-weight:800;color:var(--ink)">YOUR SMILE IS<br>SAFE IN OUR HANDS</h2>
  <p class="body abs" style="left:636px;top:3410px;width:440px">We are passionate about improving dental health and helping you achieve your brightest smile and are honoured that you're considering us for your dental needs.</p>
  <div class="btn btn-outline" style="left:636px;top:3530px;width:220px;height:44px">View Smile Gallery</div>
</section>

<!-- TESTIMONIALS -->
<section>
  <h2 class="sec abs" style="left:0;top:3770px;width:1200px;text-align:center"><b>TESTIMONIALS</b></h2>
  <div class="arrow-btn" style="left:42px;top:3983px;width:26px;height:26px;color:var(--ink)"><svg width="8" height="10" viewBox="0 0 10 12"><path d="M8 1L2 6l6 5" stroke="#1e2529" stroke-width="1.8" fill="none"/></svg></div>
  <div class="arrow-btn" style="left:1130px;top:3983px;width:26px;height:26px;color:var(--ink)"><svg width="8" height="10" viewBox="0 0 10 12"><path d="M2 1l6 5-6 5" stroke="#1e2529" stroke-width="1.8" fill="none"/></svg></div>

  <div class="t-card" style="left:112px"><div class="t-avatar" role="img" aria-label="Patient portrait"><span class="t-badge" role="img" aria-label="Ravelle ratings badge"></span></div>Sed ut perspiciatis unde omnis iste natus error sit voluptatem accusantium doloremque laudantium, totam rem aperiam, eaque ipsa</div>
  <div class="t-card" style="left:445px"><div class="t-avatar" role="img" aria-label="Patient portrait"><span class="t-badge" role="img" aria-label="Ravelle ratings badge"></span></div>Sed ut perspiciatis unde omnis iste natus error sit voluptatem accusantium doloremque laudantium, totam rem aperiam, eaque ipsa</div>
  <div class="t-card" style="left:778px"><div class="t-avatar" role="img" aria-label="Patient portrait"><span class="t-badge" role="img" aria-label="Ravelle ratings badge"></span></div>Sed ut perspiciatis unde omnis iste natus error sit voluptatem accusantium doloremque laudantium, totam rem aperiam, eaque ipsa</div>

  <div class="t-name" style="left:186px">Mara Lintel <span class="stars">★★★★★</span></div>
  <div class="t-name" style="left:519px">Mara Lintel <span class="stars">★★★★★</span></div>
  <div class="t-name" style="left:852px">Mara Lintel <span class="stars">★★★★★</span></div>
</section>

<!-- MAP -->
<section>
  <div class="photo" role="img" aria-label="Street map showing the practice location" style="left:0;top:4240px;width:1200px;height:372px;background:linear-gradient(135deg,#eceae6,#e3e1dc 50%,#ecebe8)"></div>
  <svg class="abs" style="left:604px;top:4372px" width="28" height="36" viewBox="0 0 28 36"><path d="M14 0C6 0 0 6 0 14c0 10 14 22 14 22s14-12 14-22C28 6 22 0 14 0z" fill="#d93a32"/><circle cx="14" cy="14" r="5" fill="#8b1d18"/></svg>
  <div class="btn" style="left:519px;top:4448px;width:162px;height:40px;background:var(--dark);color:var(--white);text-transform:none;font-weight:700;font-size:14px">How to find Us</div>
</section>

<!-- FOOTER -->
<footer class="footer">
  <div class="logo" style="left:110px;top:100px;color:var(--white)">
    <span class="logo-mark"></span>
    <span class="logo-name">Brambleford<br>Dental Practice</span>
  </div>
  <span class="social" style="left:117px;top:254px"></span>
  <span class="social" style="left:161px;top:254px"></span>
  <span class="social" style="left:205px;top:254px"></span>
  <span class="social" style="left:249px;top:254px"></span>

  <h4 style="left:340px;top:84px">Quick Links</h4>
  <ul style="left:342px;top:122px">
    <li>➜ Home</li><li>➜ About</li><li>➜ New Patients</li><li>➜ Treatments</li><li>➜ Fees</li><li>➜ Contact Us</li>
  </ul>

  <h4 style="left:517px;top:84px">Contact Us</h4>
  <div class="f-contact" style="left:517px;top:134px"><span class="f-ci"><svg width="12" height="16" viewBox="0 0 28 36"><path d="M14 0C6 0 0 6 0 14c0 10 14 22 14 22s14-12 14-22C28 6 22 0 14 0z" fill="#1b1c1d"/><circle cx="14" cy="14" r="5" fill="#fff"/></svg></span>12 Orchard Lane, Ashvale</div>
  <div class="f-contact" style="left:517px;top:194px"><span class="f-ci"><svg width="14" height="11" viewBox="0 0 24 18"><path fill="#1b1c1d" d="M0 0h24v18H0zM2 2v1l10 7 10-7V2z"/></svg></span>care@bramblefordental.com</div>
  <div class="f-contact" style="left:517px;top:254px"><span class="f-ci"><svg width="14" height="14" viewBox="0 0 24 24"><path fill="#1b1c1d" d="M6.6 10.8a15 15 0 006.6 6.6l2.2-2.2c.3-.3.7-.4 1-.2 1.1.4 2.3.6 3.6.6.6 0 1 .4 1 1V20c0 .6-.4 1-1 1A17 17 0 013 4c0-.6.4-1 1-1h3.5c.6 0 1 .4 1 1 0 1.3.2 2.5.6 3.6.1.3 0 .7-.2 1z"/></svg></span>+1 555 0142 7730</div>

  <h4 style="left:815px;top:84px">Sign Up To Our Newsletter</h4>
  <p class="abs" style="left:817px;top:124px;width:290px;font-size:14px;line-height:30px">Lorem ipsum dolor sit amet,consectetur adipiscing elit,adipiscing elit.</p>
  <div class="abs" style="left:818px;top:196px;width:272px;padding-bottom:10px;border-bottom:1px solid #d7d7d7;font-size:14px">Email</div>
  <div class="btn btn-light" style="left:824px;top:258px;width:145px;height:46px;text-transform:none;font-size:16px">Subscribe</div>

  <div class="abs" style="left:110px;top:419px;width:978px;height:1px;background:#8a8a8a"></div>
  <div class="abs" style="left:0;top:442px;width:1200px;text-align:center;font-size:14px">©2025.Brambleford Dental Practice.All Rights Reserved</div>
</footer>

</body>
</html>
```